Sleek wordpress site for Bramblecrest finishing works

We are a commercial job shop that serves B2B, govt & LEO and retail clients.We need a wordpress site with 6 individual pages: homepage, coating, laser engraving, laser cutting, part marking, and contact us. I have attached an outline of the desired flow and sub headings for each page. I would like to incorporate the colors of the logo through out the site to be clean and sleek enough to appeal to B2B commercial clients yet be inviting enough for retail clients.

I would like to have easy picture functionality so photographs on each page can be updated easily.

Target Market(s)

B2B industrial & Govt and Military part marking, laser engraving and coating: machine shops, aerospace companies, tool manufactures. Retail: personalized gifts, Job Shop

Coding

Coded - Design and coding required

Font styles to use
Sans Serif
Other font styles liked:
• Open to suggestion

Colors
0255a3
3176b5
eaf1f7
cfdeed
ffffff

Requirements
Must have
• Clean easy to navigate flow, separate pages as indicated on attached outline, high class feel. Great picture functionality, professional and inviting feel,
• **update: needs to be optimized for mobile, should have a gallery function. Gallery can be an additional page or embedded
Nice to have
• Social media connectivity links,
Should not have
• crappy plugins that make back-end management difficult, no blog

```html
<!DOCTYPE html>
<html lang="en">
<head>
<meta charset="utf-8">
<title>Bramblecrest Finishing Works</title>
<link href="https://fonts.googleapis.com/css2?family=Raleway:wght@400;500;600;700&family=Roboto+Slab:wght@400&family=Poppins:ital,wght@0,400;0,500;1,400&display=swap" rel="stylesheet">
<style>
:root{
  --brand:#0255a3;
  --brand-mid:#3176b5;
  --brand-deep:#0a3f8f;
  --tint:#eaf1f7;
  --tint-2:#cfdeed;
  --white:#ffffff;
  --ink:#222;
  --ink-soft:#333;
  --grey-band:#ececec;
}
*{box-sizing:border-box;margin:0;padding:0}
html,body{width:675px;height:1200px;overflow:hidden;background:var(--white)}
body{position:relative;font-family:'Poppins',sans-serif;color:var(--ink)}
.abs{position:absolute}

/* header */
.site-header{position:absolute;left:0;top:0;width:675px;height:85px;background:var(--white)}
.brand-name{left:90px;top:14px;width:120px;font-family:'Raleway',sans-serif;font-weight:700;font-size:15px;line-height:18px;color:var(--brand);text-transform:uppercase;display:flex;align-items:center;gap:6px}
.brand-name .dot{width:12px;height:12px;border-radius:50%;background:var(--brand);flex:none}
.contact-chip{top:19px;display:flex;align-items:center;gap:7px;font-family:'Raleway',sans-serif;font-size:7.5px;line-height:10px;color:var(--ink)}
.contact-chip .ic{width:18px;height:18px;border-radius:50%;background:var(--brand);display:flex;align-items:center;justify-content:center}
.main-nav{top:60px;left:232px;display:flex;gap:18px;font-family:'Raleway',sans-serif;font-weight:600;font-size:7.4px;letter-spacing:.1px}
.main-nav a{color:var(--ink);text-decoration:none}
.main-nav a.active{color:var(--brand)}

/* hero */
.hero{left:0;top:85px;width:675px;height:299px;background:radial-gradient(ellipse at 52% 55%,#8a5a24 0%,#4a3018 30%,#241a12 65%,#15110d 100%)}
.hero-title{left:0;top:90px;width:675px;text-align:center;font-family:'Raleway',sans-serif;font-weight:600;font-size:21.5px;line-height:27px;color:var(--white)}
.hero-btn{left:288px;top:149px;width:100px;height:24px;border:2px solid var(--white);border-radius:13px;background:var(--brand);color:var(--white);font-family:'Raleway',sans-serif;font-weight:600;font-size:6.8px;display:flex;align-items:center;justify-content:center}
.slider-dots{left:289px;top:272px;display:flex;gap:2px}
.slider-dots span{width:23px;height:2.5px;background:var(--white)}
.slider-dots span.dim{background:rgba(255,255,255,.4)}

/* services */
.section-title{font-family:'Roboto Slab',serif;font-weight:400;color:#333}
.services-title{left:0;top:402px;width:675px;text-align:center;font-size:15.5px}
.service{top:444px;width:120px;text-align:center}
.service .badge{width:58px;height:58px;margin:0 auto;border-radius:50%;border:1.5px solid var(--brand);padding:3px}
.service .badge div{width:100%;height:100%;border-radius:50%;background:var(--brand)}
.service h3{margin-top:10px;font-family:'Raleway',sans-serif;font-weight:600;font-size:7.6px;color:#333}
.service p{margin-top:8px;font-size:6.3px;line-height:11px;color:var(--ink)}

/* about */
.about-band{left:0;top:596px;width:675px;height:236px;background:radial-gradient(ellipse at 50% 50%,#f6f6f6 0%,var(--grey-band) 70%)}
.about-kicker{left:90px;top:633px;font-size:15px;line-height:20px}
.about-heading{left:90px;top:653px;font-size:15px;line-height:20px;color:var(--brand)}
.about-text{left:90px;top:683px;width:198px;font-size:6.2px;line-height:11.8px;color:var(--ink)}
.read-more{left:90px;top:774px;width:54px;height:20px;background:var(--brand);color:var(--white);font-family:'Raleway',sans-serif;font-weight:600;font-size:6.8px;display:flex;align-items:center;justify-content:center}
.about-photo{left:326px;top:626px;width:258px;height:172px;background:radial-gradient(ellipse at 68% 72%,#e9d6f5 0%,#7a4fc4 14%,#2d2a78 40%,#141736 75%,#0c0d1c 100%)}

/* certifications & testimonials */
.block-title{top:867px;font-size:13px}
.more-dots{top:875px;display:flex;gap:2px}
.more-dots span{width:3px;height:3px;border-radius:50%;background:var(--brand-deep)}
.cert{top:906px;width:50px;height:50px;border-radius:50%}
.quote{left:356px;top:900px;width:228px;font-style:italic;font-size:6.3px;line-height:13px;color:var(--ink)}
.avatar{left:356px;top:958px;width:35px;height:35px;border-radius:50%;background:radial-gradient(circle at 50% 45%,#cfcac4,#6f6a66)}
.author{left:400px;top:972px;font-family:'Raleway',sans-serif;font-weight:600;font-size:7px;color:var(--ink)}
.author b{color:var(--brand-mid);font-weight:600}

/* footer */
.site-footer{left:0;top:1029px;width:675px;height:171px;background:linear-gradient(160deg,#0d47a8 0%,#0a3f9a 45%,#0c4bb0 100%)}
.foot-title{top:1070px;font-family:'Roboto Slab',serif;font-size:11px;color:var(--white)}
.foot-text{font-family:'Roboto Slab',serif;font-size:6.2px;line-height:12px;color:var(--white)}
.foot-links{left:259px;top:1097px;list-style:none}
.foot-links li{font-family:'Roboto Slab',serif;font-size:6.5px;line-height:12.2px;color:var(--white)}
.foot-contact{left:342px;display:flex;gap:10px;align-items:flex-start}
.foot-contact svg{flex:none}
.social{left:489px;top:1101px;display:flex;gap:14px}
.social span{width:12px;height:12px;border-radius:2px;background:var(--white)}
</style>
</head>
<body>

<header class="site-header">
  <div class="abs brand-name"><span class="dot"></span>Bramblecrest finishing works</div>
  <div class="abs contact-chip" style="left:384px">
    <span class="ic"><svg width="8" height="8" viewBox="0 0 24 24"><path fill="#fff" d="M6.6 10.8a15 15 0 0 0 6.6 6.6l2.2-2.2c.3-.3.7-.4 1-.2 1.1.4 2.3.6 3.6.6.6 0 1 .4 1 1V20c0 .6-.4 1-1 1A17 17 0 0 1 3 4c0-.6.4-1 1-1h3.5c.6 0 1 .4 1 1 0 1.3.2 2.5.6 3.6.1.3 0 .7-.2 1z"/></svg></span>
    <span>Phone:<br>0 140 377 2960</span>
  </div>
  <div class="abs contact-chip" style="left:471px">
    <span class="ic"><svg width="8" height="8" viewBox="0 0 24 24"><path fill="#fff" d="M2 5h20v14H2z M2 5l10 8 10-8" stroke="#0255a3" stroke-width="1.5"/></svg></span>
    <span>Email:<br>hello@bramblecrestworks.com</span>
  </div>
  <nav class="abs main-nav">
    <a class="active" href="#">HOME</a>
    <a href="#">COATING</a>
    <a href="#">LASER ENGRAVING</a>
    <a href="#">LASER CUTTING</a>
    <a href="#">PART MARKING</a>
    <a href="#">CONTACT US</a>
  </nav>
</header>

<section class="abs hero" role="img" aria-label="Laser cutting head throwing a wide fan of orange sparks over a metal sheet"></section>
<h1 class="abs hero-title">WELCOME TO<br>BRAMBLECREST FINISHING</h1>
<div class="abs hero-btn">GET STARTED TODAY</div>
<div class="abs slider-dots" style="top:357px"><span></span><span></span><span class="dim"></span><span></span></div>

<h2 class="abs section-title services-title">Our Services</h2>
<div class="abs service" style="left:84px"><div class="badge"><div></div></div><h3>LASER ENGRAVING</h3><p>Seciatis unde omnis iste nasitlu tatem accusantium doloremue laua ntcusantium doloreium,mlo.</p></div>
<div class="abs service" style="left:213px"><div class="badge"><div></div></div><h3>LASER CUTTING</h3><p>Seciatis unde omnis iste nasitlu tatem accusantium doloremue laua ntcusantium doloreium,mlo.</p></div>
<div class="abs service" style="left:342px"><div class="badge"><div></div></div><h3>PART MARKING</h3><p>Seciatis unde omnis iste nasitlu tatem accusantium doloremue laua ntcusantium doloreium,mlo.</p></div>
<div class="abs service" style="left:470px"><div class="badge"><div></div></div><h3>COATINGS</h3><p>Seciatis unde omnis iste nasitlu tatem accusantium doloremue laua ntcusantium doloreium,mlo.</p></div>

<section class="abs about-band"></section>
<h2 class="abs section-title about-kicker">About</h2>
<h2 class="abs section-title about-heading">Bramblecrest Finishing</h2>
<p class="abs about-text">Lorem ipsum dolor sit amet, consectetur adipiscing elit, sed do eiusmod tempor incididunt ut labore et dolore magna aliqua. Ut enim ad minim veniam, quis nostrud exercitation ullamco laboris nisi ut aliquip ex ea commodo consequat. Duis aute irure dolor in reprehenderit in voluptate velit esse cillum dolore eu fugiat nulla pariatur. Excepteur sint occaecat cupidatat non proident, sunt in culpa qui officia deserunt mollit anim id est.</p>
<div class="abs read-more">READ MORE</div>
<div class="abs about-photo" role="img" aria-label="Laser cutter head in violet light sending sparks across a steel plate"></div>

<h2 class="abs section-title block-title" style="left:90px">Our Certifications</h2>
<div class="abs more-dots" style="left:311px"><span></span><span></span><span></span><span></span></div>
<div class="abs cert" style="left:90px;background:var(--brand)"></div>
<div class="abs cert" style="left:152px;background:#c4262e"></div>
<div class="abs cert" style="left:210px;background:var(--brand-mid)"></div>
<div class="abs cert" style="left:264px;background:#3a3a3a"></div>

<h2 class="abs section-title block-title" style="left:356px">Testimonials</h2>
<div class="abs more-dots" style="left:569px"><span></span><span></span><span></span><span></span></div>
<p class="abs quote">"Lorem ipsum dolor sit amet, consectetur adipiscing elit, sed do eiusmod tempor incididunt ut labore et dolore magna aliqua. Ut enim ad minim veniam, quis nostrud exercitation ullamco laboris nisi ut aliquip ex ea c ommodo consequat."</p>
<div class="abs avatar" role="img" aria-label="Client portrait"></div>
<div class="abs author"><b>Dara Holloway</b> Fenwick</div>

<footer class="abs site-footer"></footer>
<h3 class="abs foot-title" style="left:92px">About us</h3>
<p class="abs foot-text" style="left:91px;top:1096px;width:128px">Sed ut perspiciatis unde omnis iste na tus error sit voluptatem accusantium dol oremque laudantium, totam rem aperiam, eaque ipsa quae ab illo inventoreveritatis et quasi architecto beatae vitae</p>

<h3 class="abs foot-title" style="left:259px">Links</h3>
<ul class="abs foot-links"><li>Home</li><li>Coating</li><li>Laser engraving</li><li>Laser cutting</li><li>Part marking</li><li>contact us</li></ul>

<h3 class="abs foot-title" style="left:342px">Contact Us</h3>
<div class="abs foot-contact" style="top:1099px">
  <svg width="12" height="14" viewBox="0 0 12 14"><path d="M6 13S1 8 1 5a5 5 0 0 1 10 0c0 3-5 8-5 8z" fill="none" stroke="#fff" stroke-width=".8"/><circle cx="6" cy="5" r="1.8" fill="none" stroke="#fff" stroke-width=".8"/></svg>
  <span class="foot-text" style="line-height:10px">212 Millrace Road,<br>Oakhollow, Vantry</span>
</div>
<div class="abs foot-contact" style="top:1128px">
  <svg width="14" height="14" viewBox="0 0 24 24"><path d="M6.6 10.8a15 15 0 0 0 6.6 6.6l2.2-2.2c.3-.3.7-.4 1-.2 1.1.4 2.3.6 3.6.6.6 0 1 .4 1 1V20c0 .6-.4 1-1 1A17 17 0 0 1 3 4c0-.6.4-1 1-1h3.5c.6 0 1 .4 1 1 0 1.3.2 2.5.6 3.6.1.3 0 .7-.2 1z" fill="none" stroke="#fff" stroke-width="1.2"/></svg>
  <span class="foot-text" style="line-height:10px">8 800 412 736 20<br>8 800 519 064 37</span>
</div>
<div class="abs foot-contact" style="top:1155px">
  <svg width="14" height="11" viewBox="0 0 14 11"><rect x=".5" y=".5" width="13" height="10" fill="none" stroke="#fff" stroke-width=".8"/><path d="M.5 .5l6.5 5.5 6.5-5.5" fill="none" stroke="#fff" stroke-width=".8"/></svg>
  <span class="foot-text" style="line-height:10px">Email:<br>office@bramblecrestworks.com</span>
</div>

<h3 class="abs foot-title" style="left:489px">Follow Us</h3>
<div class="abs social"><span></span><span></span><span></span><span></span></div>
<p class="abs foot-text" style="left:489px;top:1140px">© 2018 All Rights Are Reserved.<br>Privacy Policy</p>

</body>
</html>
```